32 x 24 Swinging Real Estate Yard Sign

We are looking to design a new sign for our business to focus on the remodeling of homes to sell. We are looking to have a yard sign that gets peoples attention and is informational. The headline will be "The Secret to Top Dollar? Remodel First.". We remodel homes for sellers with no up front cost, as they simply pay at closing. This link has more info, https://bramblecresthomes.com/Remodel
The message we want to convey to those seeing the sign is we are a one stop shop, who can renovate your home and sell it for no stress. We are licensed real estate agents and licensed contractors.
Both of these license numbers and info need to be on the design:
CADRE #02794613
Contractors License #1178524
Email: info@bramblecresthomes.com
Phone: (408)614-2907
I'll attach a sample sign we have for our agents normally as well as all brand art work.
• Pantone Colors
o #172A41
Dark blue
o #4381B1
Medium blue
o #6FA6CC
Light blue
Target Market(s)
Residential Real Estate Sellers
Industry/Entity Type
Real Estate
Colors
Designer to choose colors to be used in the design.

```html
<!DOCTYPE html>
<html lang="en">
<head>
<meta charset="UTF-8">
<title>Bramblecrest Homes – Remodel First Yard Sign</title>
<link rel="stylesheet" href="https://fonts.googleapis.com/css2?family=Barlow:wght@800&family=Barlow+Semi+Condensed:wght@700&family=Poppins:wght@400;500;600&display=swap">
<style>
  :root {
    --navy: #172A41;
    --steel: #3A6A92;
    --medium-blue: #4381B1;
    --light-blue: #6FA6CC;
    --white: #FFFFFF;
    --backdrop: #C4C4C4;
  }
  * { margin: 0; padding: 0; box-sizing: border-box; }
  html, body {
    width: 956px;
    height: 1200px;
    overflow: hidden;
    background: var(--backdrop);
  }
  .yard-sign {
    position: absolute;
    left: 92px;
    top: 86px;
    width: 772px;
    height: 1028px;
    background: var(--white);
    box-shadow: 0 6px 18px rgba(0, 0, 0, 0.22);
    overflow: hidden;
  }
  .brand {
    position: absolute;
    top: 52px;
    left: 0;
    width: 100%;
    display: flex;
    justify-content: center;
    align-items: center;
    gap: 14px;
  }
  .brand-dot {
    width: 22px;
    height: 22px;
    border-radius: 50%;
    background: var(--medium-blue);
  }
  .brand-name {
    font-family: "Poppins", sans-serif;
    font-weight: 600;
    font-size: 40px;
    letter-spacing: 1px;
    color: var(--navy);
    text-transform: uppercase;
  }
  .headline-line {
    position: absolute;
    left: 0;
    width: 100%;
    text-align: center;
    font-family: "Barlow", sans-serif;
    font-weight: 800;
    line-height: 1;
    text-transform: uppercase;
  }
  .headline-question {
    font-size: 86px;
    color: var(--steel);
    letter-spacing: -0.5px;
  }
  .headline-question.line-one { top: 146px; }
  .headline-question.line-two { top: 219px; }
  .headline-answer {
    font-size: 137px;
    color: var(--navy);
    letter-spacing: -1px;
  }
  .headline-answer.line-one { top: 294px; }
  .headline-answer.line-two { top: 418px; }
  .phone-band {
    position: absolute;
    top: 554px;
    left: 0;
    width: 100%;
    height: 207px;
    background: var(--navy);
  }
  .phone-number {
    position: absolute;
    top: 46px;
    left: 0;
    width: 100%;
    text-align: center;
    font-family: "Barlow Semi Condensed", sans-serif;
    font-weight: 700;
    font-size: 127px;
    line-height: 1;
    color: var(--white);
  }
  .email-band {
    position: absolute;
    top: 761px;
    left: 0;
    width: 100%;
    height: 100px;
    background: var(--medium-blue);
    display: flex;
    justify-content: center;
    align-items: center;
  }
  .email-address {
    font-family: "Poppins", sans-serif;
    font-weight: 500;
    font-size: 45px;
    color: var(--white);
    line-height: 1;
  }
  .license-band {
    position: absolute;
    top: 861px;
    left: 0;
    width: 100%;
    height: 167px;
    background: var(--navy);
    display: flex;
    flex-direction: column;
    justify-content: center;
    align-items: center;
    gap: 6px;
  }
  .license-line {
    font-family: "Poppins", sans-serif;
    font-weight: 400;
    font-size: 41px;
    line-height: 1.15;
    color: var(--white);
  }
</style>
</head>
<body>
  <main class="yard-sign">
    <div class="brand">
      <span class="brand-dot"></span>
      <span class="brand-name">Bramblecrest Homes</span>
    </div>

    <h1 class="headline">
      <span class="headline-line headline-question line-one">The Secret To</span>
      <span class="headline-line headline-question line-two">Top Dollar?</span>
      <span class="headline-line headline-answer line-one">Remodel</span>
      <span class="headline-line headline-answer line-two">First</span>
    </h1>

    <section class="phone-band">
      <p class="phone-number">(408)614-2907</p>
    </section>

    <section class="email-band">
      <p class="email-address">info@bramblecresthomes.com</p>
    </section>

    <section class="license-band">
      <p class="license-line">CADRE #02794613</p>
      <p class="license-line">Contractors License #1178524</p>
    </section>
  </main>
</body>
</html>
```